Quillbrookes websites redesign

Www.quill-brookes.com needs to be redesigned along with updations. The incremental material will be provided for the updations. We are looking for complete redesign of the pages with the new content. The complete write up will be provided soon

Target Market(s)

Global

Coding

Coded - Design and coding required

Number of Pages Required

5+ page

Requirements
Must have
• A clean and slick design for the Consulting.
Should not have
• Too many pictures which reduces the speed of the site

```html
<!DOCTYPE html>
<html lang="en">
<head>
<meta charset="utf-8">
<title>Quillbrookes Consultancy</title>
<link href="https://fonts.googleapis.com/css2?family=Open+Sans:ital,wght@0,400;0,600;0,700;1,400&display=swap" rel="stylesheet">
<style>
:root{
  --navy:#243553;
  --navy-band:#2b4668;
  --blue:#3aa6cc;
  --blue-soft:#5bb8d8;
  --text:#4a4a4a;
  --muted:#777;
  --rule:#e2e2e2;
  --contact-bg:#e8e8e8;
  --footer-bg:#2e2e2e;
  --white:#fff;
}
*{margin:0;padding:0;box-sizing:border-box}
html,body{width:718px;height:1200px;overflow:hidden;background:var(--white)}
body{font-family:"Open Sans",Arial,sans-serif;color:var(--text);position:relative}
.abs{position:absolute}
.center{text-align:center;left:0;width:718px}

/* header */
.site-header{position:absolute;left:0;top:0;width:718px;height:59px;background:var(--white);border-top:2px solid var(--blue);box-shadow:0 1px 3px rgba(0,0,0,.08);z-index:2}
.brand{position:absolute;left:60px;top:18px;display:flex;align-items:center;gap:6px;font-size:17px;color:var(--navy);font-weight:400}
.brand-dot{width:16px;height:16px;border-radius:50%;background:var(--navy)}
.nav-active{position:absolute;left:266px;top:0;width:64px;height:57px;background:#f4f4f4;border-bottom:3px solid var(--blue)}
.nav a{position:absolute;top:25px;font-size:6.5px;color:#333;text-decoration:none;letter-spacing:.1px}
.nav a.active{color:var(--blue);left:297px}

/* hero */
.hero{position:absolute;left:0;top:59px;width:718px;height:303px;background:linear-gradient(100deg,#bcd3e2 0%,#dfe9ef 35%,#e9eef1 60%,#c7d4de 100%)}
.hero-title{top:174px;font-size:18px;font-weight:700;color:#111;letter-spacing:.4px}
.hero-text{top:203px;font-size:8.6px;line-height:14.4px;color:#222}
.stat{position:absolute;top:244px;width:37px;height:37px;border-radius:50%;background:#3a3f47;border:3px solid;color:#fff;font-size:6.2px;display:flex;align-items:center;justify-content:center}
.arrow{position:absolute;top:208px;width:22px;height:22px;border-radius:50%;background:rgba(120,120,120,.55)}

/* about */
.section-title{font-size:14px;font-weight:600;color:var(--navy)}
.about-text{left:80px;width:558px;text-align:center;font-size:7px;line-height:14.4px;color:var(--muted)}
.btn{position:absolute;top:507px;height:26px;width:98px;border-radius:2px;color:#fff;font-size:7px;font-weight:600;display:flex;align-items:center;justify-content:center}
.btn-dark{left:257px;background:var(--navy)}
.btn-blue{left:363px;background:var(--blue-soft)}
.rule{position:absolute;left:58px;top:562px;width:601px;height:1px;background:var(--rule)}

/* case studies */
.case{position:absolute;top:637px;width:190px;text-align:center}
.case-icon{width:86px;height:86px;margin:3px auto 0;border-radius:50%;border:3px solid #e4e4e4;display:flex;align-items:center;justify-content:center}
.case h3{margin-top:12px;font-size:7.6px;font-weight:600;color:#222;letter-spacing:.2px}
.case p{margin-top:5px;font-size:6.2px;line-height:12.8px;color:var(--muted)}
.col-rule{position:absolute;top:637px;width:1px;height:153px;background:var(--rule)}

/* founder */
.founder{position:absolute;left:0;top:815px;width:718px;height:189px;background:var(--navy-band)}
.founder-title{top:845px;font-size:14px;font-weight:600;color:#fff}
.founder-photo{position:absolute;left:60px;top:876px;width:98px;height:98px;border-radius:50%;border:3px solid #fff;background:linear-gradient(160deg,#8b3a2d,#3a1c1a 70%)}
.quote{position:absolute;left:205px;top:886px;width:456px;font-size:6.9px;line-height:15.2px;font-style:italic;color:#e7edf4}
.quote-mark{font-size:14px;color:#8ea4bd;font-style:italic}
.founder-name{left:206px;top:944px;font-size:7.6px;color:#fff}
.founder-role{left:206px;top:957px;font-size:6.4px;color:#cfd8e2}

/* contact */
.contact{position:absolute;left:0;top:1004px;width:718px;height:154px;background:var(--contact-bg)}
.h-small{font-size:8.6px;font-weight:600;color:#222}
.addr{left:69px;top:1049px;font-size:6.8px;line-height:15.5px;color:#555}
.phone{font-size:6.8px;color:#555}
.field{position:absolute;background:var(--navy);border-radius:2px;color:#fff;font-size:6.4px;padding:5px 7px}
.send{position:absolute;left:571px;top:1112px;width:88px;height:25px;background:var(--blue-soft);border-radius:2px;color:#fff;font-size:6.8px;font-weight:600;display:flex;align-items:center;justify-content:center}

/* footer */
.site-footer{position:absolute;left:0;top:1158px;width:718px;height:42px;background:var(--footer-bg)}
.foot-dot{position:absolute;left:60px;top:1168px;width:20px;height:20px;border-radius:50%;background:#555}
.foot-links{left:90px;top:1167px;font-size:6.2px;color:#bbb}
.foot-copy{left:90px;top:1181px;font-size:5.8px;color:#999}
.connect{left:516px;top:1173px;font-size:5.8px;color:#bbb}
.social{position:absolute;top:1168px;width:18px;height:18px;border-radius:2px}
.page-code{left:695px;top:1173px;font-size:6.4px;color:#999}
</style>
</head>
<body>

<header class="site-header">
  <div class="brand"><span class="brand-dot"></span>Quillbrookes</div>
  <div class="nav-active"></div>
  <nav class="nav">
    <a class="active" href="#">HOME</a>
    <a href="#" style="left:350px">FOUNDER</a>
    <a href="#" style="left:414px">CONSULTANCY</a>
    <a href="#" style="left:494px">SYSTEM</a>
    <a href="#" style="left:552px">CASE STUDIES</a>
    <a href="#" style="left:629px">CONTACT</a>
  </nav>
</header>

<section class="hero" role="img" aria-label="Hands holding a tablet showing a glowing world globe"></section>
<div class="arrow" style="left:21px"></div>
<div class="arrow" style="left:674px"></div>
<h1 class="abs center hero-title">WORLD MERCHANDISING TRADE</h1>
<p class="abs center hero-text">Quillbrookes Consultancy Limited capitalizes on synergies arising from trade and investment linkages<br>between countries and knowledge of traditional and non-traditional...</p>
<div class="stat" style="left:255px;border-color:#3aa6cc">0-250</div>
<div class="stat" style="left:313px;border-color:#d9457a">250-500</div>
<div class="stat" style="left:372px;border-color:#2fb59a">500-1000</div>
<div class="stat" style="left:426px;border-color:#3aa6cc">&gt;1000</div>

<h2 class="abs center section-title" style="top:385px">ABOUT US</h2>
<p class="abs about-text" style="top:411px">Quillbrookes Consultancy Limited capitalizes on synergies arising from trade and investment linkages between countries and knowledge of traditional and non-traditional pools of liquidity to provide consultancy services to Emerging country banks, Corporates and SMEs.</p>
<p class="abs about-text" style="top:447px">The Consultancy provides bank neutral views to Corporates and SMEs in Asian emerging markets and helps in improving financial structure and efficient use of funds. Our endeavor is to provide a distinct bottom line advantage to our clients. The primary focus is in regionalisation of the banking relationship across the globe, providing structured finance solutions and off balance sheet solutions.</p>
<div class="btn btn-dark">READ MORE INFO!</div>
<div class="btn btn-blue">GET START TODAY!</div>
<div class="rule"></div>

<h2 class="abs center section-title" style="top:585px">CASE STUDIES</h2>
<p class="abs center" style="top:608px;font-size:8.2px;color:#666">Some of the deals completed by QCL are summarised below to describe the range of activities undertaken with Corporates</p>

<div class="case" style="left:53px">
  <div class="case-icon" style="background:#42a9d3;border-color:#d3ebf5">
    <svg width="34" height="26" viewBox="0 0 34 26"><rect x="2" y="2" width="30" height="22" rx="3" fill="none" stroke="#fff" stroke-width="2.5"/><rect x="2" y="9" width="30" height="3" fill="#fff"/><rect x="6" y="16" width="8" height="2.5" fill="#fff"/></svg>
  </div>
  <h3 style="color:#3aa6cc">EXPORT CREDIT AGENCY</h3>
  <p>Sed ut perspiciatis unde omnis iste natus error sit volup-<br>tatem accusantium doloremque laudantium, totam rem<br>aperiam, eaque ipsa quae...</p>
</div>
<div class="col-rule" style="left:254px"></div>
<div class="case" style="left:264px">
  <div class="case-icon" style="background:var(--navy)">
    <svg width="30" height="28" viewBox="0 0 30 28"><rect x="2" y="12" width="6" height="14" rx="1" fill="#fff"/><path d="M10 13 L15 3 C17 1 20 2 19 6 L18 10 H26 C28 10 29 12 28 14 L25 24 C24 26 23 26 21 26 H10 Z" fill="#fff"/></svg>
  </div>
  <h3>BACKED LONG TERM</h3>
  <p>Sed ut perspiciatis unde omnis iste natus error sit volup-<br>tatem accusantium doloremque laudantium, totam rem<br>aperiam, eaque ipsa quae...</p>
</div>
<div class="col-rule" style="left:466px"></div>
<div class="case" style="left:475px">
  <div class="case-icon" style="background:var(--navy)"><span style="color:#fff;font-size:30px;font-weight:700">$</span></div>
  <h3>PROJECT FINANCING</h3>
  <p>Sed ut perspiciatis unde omnis iste natus error sit volup-<br>tatem accusantium doloremque laudantium, totam rem<br>aperiam, eaque ipsa quae...</p>
</div>

<section class="founder" role="img" aria-label="Faint world map pattern behind the founder section"></section>
<h2 class="abs center founder-title">FOUNDER</h2>
<div class="founder-photo" role="img" aria-label="Portrait of the founder speaking at a podium"></div>
<p class="quote"><span class="quote-mark">&ldquo;</span>&nbsp;&nbsp; Ms. Meera Khanna is the founder director of Quillbrookes Consultancy Limited (QCL) based at Hong Kong. Meera worked as the Alternate Chief Executive of Northbay Bank, Hong Kong Branch until Jan 2013, heading Corporate Banking business in North Asia and Export Credit Agency business globally. During her tenure, both the businesses increased multifold. <span class="quote-mark">&rdquo;</span></p>
<p class="abs founder-name">Meera Khanna</p>
<p class="abs founder-role">Our Founder</p>

<section class="contact"></section>
<h3 class="abs h-small" style="left:58px;top:1026px">CONTACT US</h3>
<svg class="abs" style="left:58px;top:1052px" width="6" height="9" viewBox="0 0 6 9"><path d="M3 0 C1.3 0 0 1.3 0 3 C0 5 3 9 3 9 C3 9 6 5 6 3 C6 1.3 4.7 0 3 0Z" fill="#333"/><circle cx="3" cy="3" r="1.1" fill="#e8e8e8"/></svg>
<p class="abs addr">Quillbrookes Consultancy Ltd<br>Unit 04, 9th Floor, Harbourview<br>Tower,<br>18 Canton Lane, Kowloon<br>Hong Kong</p>
<svg class="abs" style="left:197px;top:1052px" width="8" height="8" viewBox="0 0 8 8"><path d="M1.5 0 L3 2 L2 3 C2.6 4.4 3.6 5.4 5 6 L6 5 L8 6.5 L6.8 8 C3 7.6 0.4 5 0 1.2Z" fill="#333"/></svg>
<p class="abs phone" style="left:207px;top:1049px">+852-2755 0193 (landline)</p>
<svg class="abs" style="left:197px;top:1076px" width="8" height="8" viewBox="0 0 8 8"><rect x="0" y="2" width="8" height="6" rx="1" fill="#333"/><rect x="2" y="0" width="4" height="3" fill="#333"/><rect x="2" y="4" width="4" height="2" fill="#e8e8e8"/></svg>
<p class="abs phone" style="left:207px;top:1074px">+852-2755 0194 (fax)</p>

<h3 class="abs h-small" style="left:335px;top:1026px">QUERY</h3>
<div class="field" style="left:335px;top:1051px;width:159px;height:17px">Name*</div>
<div class="field" style="left:500px;top:1051px;width:159px;height:17px">E-mail*</div>
<div class="field" style="left:335px;top:1074px;width:324px;height:33px">Message*</div>
<div class="send">SEND MESSAGE</div>

<footer class="site-footer"></footer>
<div class="foot-dot"></div>
<p class="abs foot-links">HOME &nbsp;|&nbsp; FOUNDER &nbsp;|&nbsp; CONSULTANCY &nbsp;|&nbsp; SYSTEM &nbsp;|&nbsp; CASE STUDIES &nbsp;|&nbsp; CONTACT</p>
<p class="abs foot-copy">COPYRIGHTS © QUILL-BROOKES . 2016 | ALLRIGHTS RESERVED.</p>
<p class="abs connect">CONNECT WITH US:</p>
<div class="social" style="left:577px;background:#3b5a9a"></div>
<div class="social" style="left:599px;background:#2d9fe0"></div>
<div class="social" style="left:620px;background:#d9382b"></div>
<div class="social" style="left:642px;background:#f29a1d"></div>
<p class="abs page-code">C11</p>

</body>
</html>
```